Investment company needing business card

We are wanting a business card which looks sharp and easy on the eye. We are thinking of having a business card with the logo embossed on it, to really make it stand out. We will only have a small amount of information of the business card, person's name, position, email address and phone number

Contact Information for Business Card

Danielle Frost
Executive Assistant
+64 21 473 5162
danielf@harwickpartners.co.nz

Requirements
Must have
• Embossed logo
Should not have
• Not to be busy

```html
<!DOCTYPE html>
<html lang="en">
<head>
<meta charset="utf-8">
<title>Harwick Partners – Business Card</title>
<link href="https://fonts.googleapis.com/css2?family=Oswald:wght@400;500&family=Roboto+Condensed:wght@400&display=swap" rel="stylesheet">
<style>
  :root {
    --page-bg: #2b2b2b;
    --card-top: #1c1c1c;
    --card-bottom: #050505;
    --brand-green: #2fc486;
    --text-white: #f2f2f2;
    --text-muted: #cfcfcf;
  }
  html, body {
    margin: 0;
    padding: 0;
    width: 1200px;
    height: 896px;
    overflow: hidden;
    background: var(--page-bg);
  }
  .canvas {
    position: relative;
    width: 1200px;
    height: 896px;
  }
  .card {
    position: absolute;
    top: 305px;
    width: 500px;
    height: 286px;
    border-radius: 18px;
    background: linear-gradient(155deg, var(--card-top) 0%, var(--card-bottom) 60%);
    box-shadow: 0 18px 40px rgba(0,0,0,0.55);
    overflow: hidden;
  }
  .card--front { left: 70px; }
  .card--back { left: 630px; }

  .brand {
    position: absolute;
    display: flex;
    align-items: center;
    gap: 12px;
    font-family: "Oswald", sans-serif;
    font-weight: 500;
    color: var(--brand-green);
    text-transform: uppercase;
    letter-spacing: 1px;
    white-space: nowrap;
  }
  .brand__square {
    background: var(--brand-green);
    flex: none;
  }
  .card--front .brand {
    left: 50%;
    top: 50%;
    transform: translate(-50%, -50%);
    font-size: 40px;
  }
  .card--front .brand__square { width: 34px; height: 34px; }
  .card--back .brand {
    left: 34px;
    top: 44px;
    font-size: 24px;
    gap: 9px;
  }
  .card--back .brand__square { width: 20px; height: 20px; }

  .edge-tab {
    position: absolute;
    right: 0;
    top: 26px;
    display: flex;
  }
  .edge-tab__green { width: 34px; height: 22px; background: var(--brand-green); }
  .edge-tab__white { width: 6px; height: 22px; background: var(--text-white); margin-left: 4px; }

  .person {
    position: absolute;
    right: 52px;
    top: 22px;
    text-align: right;
  }
  .person__name {
    font-family: "Oswald", sans-serif;
    font-weight: 400;
    font-size: 26px;
    color: var(--brand-green);
    text-transform: uppercase;
    line-height: 1.1;
  }
  .person__role {
    font-family: "Roboto Condensed", sans-serif;
    font-size: 14px;
    color: var(--text-white);
    margin-top: 2px;
  }

  .rule {
    position: absolute;
    left: 34px;
    right: 52px;
    top: 178px;
    height: 1px;
    background: var(--brand-green);
  }

  .contacts {
    position: absolute;
    left: 34px;
    top: 192px;
    margin: 0;
    padding: 0;
    list-style: none;
    font-family: "Roboto Condensed", sans-serif;
    font-size: 14px;
    color: var(--text-muted);
  }
  .contacts li {
    display: flex;
    align-items: center;
    gap: 8px;
    line-height: 22px;
  }
  .contacts svg { width: 11px; height: 11px; flex: none; }
</style>
</head>
<body>
<div class="canvas">

  <section class="card card--front" aria-label="Card front">
    <div class="brand"><span class="brand__square"></span>Harwick Partners</div>
  </section>

  <section class="card card--back" aria-label="Card back">
    <div class="brand"><span class="brand__square"></span>Harwick Partners</div>

    <div class="edge-tab"><span class="edge-tab__green"></span><span class="edge-tab__white"></span></div>

    <div class="person">
      <div class="person__name">Danielle Frost</div>
      <div class="person__role">Executive Assistant</div>
    </div>

    <div class="rule"></div>

    <ul class="contacts">
      <li>
        <svg viewBox="0 0 12 12" aria-hidden="true"><path d="M2.5 1 L4.5 1 L5.2 3.6 L4 4.6 Q5 6.9 7.4 8 L8.4 6.8 L11 7.5 L11 9.5 Q11 11 9.5 11 Q1 10.5 1 2.5 Q1 1 2.5 1 Z" fill="var(--brand-green)"/></svg>
        <span>+64 21 473 5162</span>
      </li>
      <li>
        <svg viewBox="0 0 12 12" aria-hidden="true"><rect x="1" y="2.5" width="10" height="7" fill="none" stroke="var(--brand-green)" stroke-width="1.2"/><path d="M1 2.5 L6 6.5 L11 2.5" fill="none" stroke="var(--brand-green)" stroke-width="1.2"/></svg>
        <span>danielf@harwickpartners.co.nz</span>
      </li>
      <li>
        <svg viewBox="0 0 12 12" aria-hidden="true"><circle cx="6" cy="6" r="4.8" fill="none" stroke="var(--brand-green)" stroke-width="1.2"/><path d="M1.2 6 H10.8 M6 1.2 Q3.5 6 6 10.8 M6 1.2 Q8.5 6 6 10.8" fill="none" stroke="var(--brand-green)" stroke-width="1"/></svg>
        <span>www.harwickpartners.co.nz</span>
      </li>
    </ul>
  </section>

</div>
</body>
</html>
```